"Vine Hollow Excursions" is a top notch Santa Barbara County Wine Tour company.

We provide scenic, boutique and custom wine tours. I need the card to be clean and classy. I will provide our logo. I would like the logo to cover the back side of the card as an option and would like to see a couple color options other then our signature green and gold. I would like to see some creative options and let the designers come up with options.
I need cards for myself and my team. The final design should communicate "An authentic and boutique wine tour experience"
Please use my website for reference www.vinehollowexcursions.example

Target Market(s)

We have a wide range of clients from millennials to baby boomers

Industry/Entity Type

Tour

Contact Information for Business Card

Contact info:
Dale Morton
805-219-6384
info@vinehollowexcursions.example
vinehollowexcursions.example

Colors

Designer to choose colors to be used in the design.

Requirements
Must have
• my logo
Nice to have
• *I would like to have the backside side with the logo and the company statement
• "An authentic and boutique wine tour experience" as an option.
• *I would also like to see what the designers can create!
• *I would like to see an option that incorporates or social: instagram, yelp, trip advisor
Should not have
• I do not want it too busy.

```html
<!DOCTYPE html>
<html lang="en">
<head>
<meta charset="utf-8">
<title>Vine Hollow Excursions – Business Card</title>
<link rel="stylesheet" href="https://fonts.googleapis.com/css2?family=Cinzel:wght@400;600&family=Roboto:wght@300;400&display=swap">
<style>
  :root {
    --backdrop: #3a302b;
    --vine-green: #22714a;
    --vine-green-deep: #1a5c3a;
    --ink-green: #2f6a3c;
    --gold: #a89070;
    --paper: #ffffff;
    --text-grey: #555555;
  }
  * { box-sizing: border-box; margin: 0; padding: 0; }
  html, body { width: 1200px; height: 800px; overflow: hidden; }
  body {
    background: var(--backdrop);
    position: relative;
    font-family: "Roboto", Arial, sans-serif;
  }
  .card {
    position: absolute;
    top: 245px;
    width: 540px;
    height: 310px;
    box-shadow: 0 8px 24px rgba(0,0,0,.45);
  }
  /* Back side */
  .card-back {
    left: 40px;
    background: var(--vine-green);
    display: flex;
    flex-direction: column;
    align-items: center;
    justify-content: center;
    gap: 14px;
  }
  .card-back .brand-name {
    font-family: "Cinzel", Georgia, serif;
    font-weight: 400;
    font-size: 34px;
    letter-spacing: 2px;
    color: var(--vine-green-deep);
    text-align: center;
  }
  .card-back .brand-mark {
    width: 26px; height: 26px;
    border-radius: 50%;
    background: var(--vine-green-deep);
  }
  /* Front side */
  .card-front {
    left: 620px;
    background: var(--paper);
  }
  .front-brand {
    position: absolute;
    right: 34px;
    top: 118px;
    display: flex;
    align-items: center;
    gap: 10px;
  }
  .front-brand .brand-mark {
    width: 18px; height: 18px;
    border-radius: 50%;
    background: var(--vine-green);
  }
  .front-brand .brand-name {
    font-family: "Cinzel", Georgia, serif;
    font-weight: 400;
    font-size: 19px;
    letter-spacing: 1px;
    color: var(--gold);
  }
  .person {
    position: absolute;
    left: 30px;
    top: 120px;
  }
  .person-name {
    font-family: "Cinzel", Georgia, serif;
    font-weight: 600;
    font-size: 20px;
    color: var(--ink-green);
    letter-spacing: .5px;
  }
  .person-title {
    font-size: 12px;
    font-weight: 400;
    color: #333;
    letter-spacing: .5px;
    margin-top: 2px;
  }
  .divider {
    position: absolute;
    left: 28px;
    right: 28px;
    top: 172px;
    height: 1.5px;
    background: var(--ink-green);
  }
  .contact {
    position: absolute;
    left: 30px;
    right: 20px;
    top: 186px;
    font-size: 11.5px;
    font-weight: 300;
    color: var(--text-grey);
    line-height: 1.9;
  }
  .contact .label { color: var(--ink-green); font-weight: 400; }
  .contact .sep { margin: 0 5px; color: var(--ink-green); }
  .social-dot {
    display: inline-block;
    width: 8px; height: 8px;
    border-radius: 50%;
    background: var(--ink-green);
    margin-right: 4px;
    vertical-align: middle;
  }
</style>
</head>
<body>
  <section class="card card-back" aria-label="Card back">
    <span class="brand-mark"></span>
    <div class="brand-name">Vine Hollow Excursions</div>
  </section>

  <section class="card card-front" aria-label="Card front">
    <div class="front-brand">
      <span class="brand-mark"></span>
      <span class="brand-name">Vine Hollow Excursions</span>
    </div>

    <div class="person">
      <div class="person-name">DALE MORTON</div>
      <div class="person-title">TRIP ADVISOR</div>
    </div>

    <div class="divider"></div>

    <div class="contact">
      <div>
        <span class="label">P :</span> 805-219-6384<span class="sep">|</span>
        <span class="label">E :</span> info@vinehollowexcursions.example<span class="sep">|</span>
        <span class="label">W :</span> www.vinehollowexcursions.example
      </div>
      <div>
        <span class="social-dot"></span>: /vinehollowexcursions<span class="sep">|</span>
        <span class="social-dot"></span>: @vinehollowexcursions<span class="sep">|</span>
        <span class="social-dot"></span>: @sbvinehollow
      </div>
    </div>
  </section>
</body>
</html>
```